Brightline Energy Product Distribution Brochure

We are looking to have our current brochure for our customers completely redesigned...the idea is to present the relevant information in an attractive way . Our website is brightlineenergyco.example where you can find more information about us. We have included a file with a rough idea of the page order and what each should include but feel free to adapt based on design. The example provided is only for context and doesnt have to be maintained. We will be using the brochure both digitally and in print form. As long as it reads easily and is eye catching, the design can be horizontal or vertical.Final deliverable should be indesign file.

"Our Brands" page: should be limited to one page (space being enough) where it has the header for each one (for example diesel generators) space for one or two lines of text and then the corresponding logos for each of the five categories
Updates

For those asking: the "our brands" page should be a single page layout where there is a header with the corresponding section and space for maybe one line of text followed by the two logos for that category. Each of the product pages should be similar in fashion to the one in the document attached: a photo of the product with some white space and space for the text to be included. We will be posting additional examples today

Target Market(s)

We want to present it to customers both digitally and in print so they can see our products

Industry/Entity Type

Power Generation

Font styles to use
Serif

Requirements
Must have
• Eye catching and able to present the information in a presentable fashion. Rest is up to you.
Nice to have
• Should incorporate the colors of our logo but can also add other depending on design

```html
<!DOCTYPE html>
<html lang="en">
<head>
<meta charset="utf-8">
<title>Brightline Energy – Distributor Program Guide</title>
<link rel="stylesheet" href="https://fonts.googleapis.com/css2?family=Work+Sans:wght@200;400;600;800;900&display=swap">
<style>
  :root {
    --backdrop: #d1d2d4;
    --paper: #ffffff;
    --charcoal: #4a4647;
    --ink: #3a3637;
    --sun: #fcc419;
    --sun-bright: #ffdd00;
    --amber-deep: #5a4220;
    --amber-mid: #a07a3a;
    --amber-light: #d9a94a;
  }
  * { box-sizing: border-box; margin: 0; padding: 0; }
  html, body {
    width: 1149px; height: 1200px; overflow: hidden;
    background: var(--backdrop);
    font-family: "Work Sans", Arial, sans-serif;
  }
  .cover {
    position: absolute; left: 111px; top: 0;
    width: 927px; height: 1200px;
    background: var(--paper);
    overflow: hidden;
  }
  .cover-art { position: absolute; inset: 0; width: 100%; height: 100%; display: block; }
  .cover-title {
    position: absolute; left: 76px; top: 108px;
    color: var(--paper);
    font-weight: 900; font-size: 60px; line-height: 68px;
    letter-spacing: 0.5px; text-transform: uppercase;
  }
  .title-rule {
    position: absolute; left: 76px; top: 262px;
    width: 125px; height: 2px; background: var(--paper);
  }
  .cover-subtitle {
    position: absolute; left: 76px; top: 290px;
    color: var(--paper);
    font-weight: 200; font-size: 42px; line-height: 60px;
    text-transform: uppercase;
  }
  .company-address {
    position: absolute; left: 67px; top: 1060px;
    color: var(--ink);
    font-size: 15px; line-height: 20px; font-weight: 400;
  }
  .company-phone {
    display: block; margin-top: 10px;
    color: var(--sun); font-weight: 800; font-size: 16px;
  }
  .brand-name {
    position: absolute; right: 83px; top: 1088px;
    display: flex; align-items: center; gap: 14px;
  }
  .brand-mark { width: 26px; height: 26px; background: var(--sun); }
  .brand-word {
    color: var(--charcoal);
    font-weight: 400; font-size: 30px; letter-spacing: 2px;
    text-transform: uppercase;
  }
</style>
</head>
<body>
  <main class="cover">
    <svg class="cover-art" viewBox="0 0 612 792" preserveAspectRatio="none" aria-hidden="false">
      <defs>
        <linearGradient id="plantTone" x1="0" y1="0" x2="0.4" y2="1">
          <stop offset="0" stop-color="#b89458"/>
          <stop offset="0.35" stop-color="var(--amber-mid)"/>
          <stop offset="0.75" stop-color="var(--amber-deep)"/>
          <stop offset="1" stop-color="#3d2e1c"/>
        </linearGradient>
        <linearGradient id="workshopTone" x1="0" y1="0" x2="1" y2="1">
          <stop offset="0" stop-color="#c9d3dc"/>
          <stop offset="0.6" stop-color="#8fa2b3"/>
          <stop offset="1" stop-color="#d9762f"/>
        </linearGradient>
        <linearGradient id="refineryTone" x1="0" y1="0" x2="1" y2="1">
          <stop offset="0" stop-color="#e6e8ea"/>
          <stop offset="0.6" stop-color="#9aa1a8"/>
          <stop offset="1" stop-color="#2f3a55"/>
        </linearGradient>
      </defs>

      <rect width="612" height="792" fill="var(--paper)"/>

      <g role="img" aria-label="Industrial steel plant lit at dusk">
        <polygon points="0,0 612,0 612,262 262,668 210,684 0,476" fill="url(#plantTone)"/>
      </g>

      <line class="band-white" x1="612" y1="298" x2="330" y2="580" stroke="var(--paper)" stroke-width="20"/>
      <line class="band-charcoal" x1="612" y1="266" x2="360" y2="518" stroke="var(--charcoal)" stroke-width="26"/>
      <line class="band-sun" x1="0" y1="402" x2="266" y2="674" stroke="var(--sun)" stroke-width="22"/>
      <line class="band-sun" x1="612" y1="328" x2="252" y2="688" stroke="var(--sun-bright)" stroke-width="22"/>
      <line class="band-charcoal" x1="0" y1="474" x2="206" y2="680" stroke="var(--charcoal)" stroke-width="26"/>

      <polygon class="accent-diamond" points="400,505 418,523 400,541 382,523" fill="var(--sun)"/>

      <g role="img" aria-label="Technicians working at generator control equipment">
        <polygon points="442,368 522,448 442,528 362,448" fill="url(#workshopTone)"/>
      </g>
      <g role="img" aria-label="Engineers walking through a refinery pipe yard">
        <polygon points="336,478 416,558 336,638 256,558" fill="url(#refineryTone)"/>
      </g>

      <rect class="footer-strip" x="0" y="783" width="612" height="9" fill="var(--charcoal)"/>
    </svg>

    <h1 class="cover-title">Distributor<br>Program Guide</h1>
    <div class="title-rule"></div>
    <p class="cover-subtitle">Diesel Generators<br>Alternators &amp; Parts</p>

    <address class="company-address">
      Brightline Energy Limited, Inc.<br>
      4120 Harbor Point Avenue<br>
      Tampa, FL 33602, USA
      <span class="company-phone">1-800-555-0148</span>
    </address>

    <div class="brand-name">
      <span class="brand-mark"></span>
      <span class="brand-word">Brightline Energy</span>
    </div>
  </main>
</body>
</html>
```